Modern Business Card for Larkwell 2018

Our company assumes the best about people. We are creating an online community of entrepreneurs and business leaders who struggle with marketing their business online.

This business card should POP! We recently got a new logo and are launching a new website next month, so our business cards should make a statement that feels:
-Fresh
-Smart
-Trustworthy
-Fun

Target Market(s)

small business owners, entrepreneurs

Industry/Entity Type

Digital Marketing

Contact Information for Business Card

Dimensions: 3.5" x 2"

Font styles to use
Sans Serif

Colors
f37122
ffffff

Requirements
Must have
• We need a business card with a modern, bold design. We will use one side of the card as a lead-generation offer, so text on one side will need to fit up to 140 characters. The business card should stick to our core colors (orange, black, and white).
Nice to have
• We think a vertical "portrait" design could be interesting.
Should not have
• Should not look like a traditional business card. The round icon should stand out from a distance.

```html
<!DOCTYPE html>
<html lang="en">
<head>
<meta charset="utf-8">
<title>Larkwell Business Card</title>
<link rel="stylesheet" href="https://fonts.googleapis.com/css2?family=Roboto:wght@400;500;900&family=Roboto+Condensed:wght@400&display=swap">
<style>
  :root {
    --orange: #f37122;
    --white: #ffffff;
    --ink: #2b2b2b;
    --grey: #555555;
    --rule: #8a8a8a;
    --card-dark: #2d2927;
    --map-tone: #3b3634;
    --stage: #e9e9e9;
    --soft-text: #d9d6d4;
  }
  * { margin: 0; padding: 0; box-sizing: border-box; }
  html, body { width: 1200px; height: 900px; overflow: hidden; }
  body {
    background: var(--stage);
    font-family: "Roboto", sans-serif;
    position: relative;
  }
  .card {
    position: absolute;
    left: 250px;
    width: 700px;
    height: 400px;
    border-radius: 22px;
    overflow: hidden;
  }
  .card-front { top: 40px; background: var(--white); }
  .card-back { top: 460px; background: var(--card-dark); }

  /* front */
  .person { position: absolute; left: 48px; top: 58px; }
  .person-name {
    color: var(--orange);
    font-size: 34px;
    font-weight: 500;
    letter-spacing: 1px;
    text-transform: uppercase;
  }
  .person-title { color: var(--grey); font-size: 20px; margin-top: 2px; }
  .front-rule {
    position: absolute; left: 40px; right: 40px; top: 200px;
    height: 2px; background: var(--rule);
  }
  .contact {
    position: absolute; left: 48px; top: 226px;
    color: var(--ink); font-size: 18px; line-height: 26px;
    list-style: none;
  }
  .contact-address { margin-bottom: 6px; }
  .contact-item { display: flex; align-items: center; gap: 10px; }
  .contact-item svg { width: 14px; height: 14px; flex: none; }
  .web-name { color: var(--orange); }
  .brand {
    position: absolute; right: 48px; top: 112px;
    display: flex; align-items: center; gap: 12px;
  }
  .brand-dot { width: 38px; height: 38px; border-radius: 50%; background: var(--orange); }
  .brand-name {
    font-weight: 900; font-size: 42px; color: var(--ink);
    letter-spacing: 1px; text-transform: uppercase;
  }

  /* back */
  .map-area {
    position: absolute; inset: 30px 40px 30px 40px;
    border-radius: 12px;
    background: radial-gradient(ellipse at 50% 45%, var(--map-tone), var(--card-dark) 75%);
  }
  .back-brand {
    position: absolute; left: 0; right: 0; top: 70px;
    display: flex; justify-content: center; align-items: center; gap: 18px;
  }
  .back-brand .brand-dot { width: 64px; height: 64px; }
  .back-brand .brand-name { font-size: 66px; color: var(--soft-text); }
  .offer {
    position: absolute; left: 0; right: 0; top: 198px;
    text-align: center; color: var(--soft-text);
    font-size: 20px; line-height: 28px;
  }
  .back-rule {
    position: absolute; left: 90px; right: 90px; top: 272px;
    height: 2px; background: var(--orange);
  }
  .tagline {
    position: absolute; left: 0; right: 0; top: 290px;
    text-align: center; color: var(--white);
    font-family: "Roboto Condensed", sans-serif;
    font-size: 22px; letter-spacing: 0.5px;
  }
</style>
</head>
<body>
  <section class="card card-front">
    <div class="person">
      <h1 class="person-name">Dana Whitfield</h1>
      <p class="person-title">Story Marketing Coach</p>
    </div>
    <div class="brand">
      <span class="brand-dot"></span>
      <span class="brand-name">Larkwell</span>
    </div>
    <div class="front-rule"></div>
    <ul class="contact">
      <li class="contact-address">AZ1010, 8/21 Nizami St.<br>Baku city, Azerbaijan</li>
      <li class="contact-item">
        <svg viewBox="0 0 14 14" aria-hidden="true"><path d="M3 1 L5.5 1 L6.5 4 L5 5.2 Q6.3 8 8.8 9 L10 7.5 L13 8.5 L13 11 Q12.5 13 10.5 13 Q1 12 1 3.5 Q1 1.5 3 1Z" fill="#f37122"/></svg>
        <span>(804) 555-0142</span>
      </li>
      <li class="contact-item">
        <svg viewBox="0 0 14 14" aria-hidden="true"><rect x="1" y="3" width="12" height="8" rx="1" fill="none" stroke="#f37122" stroke-width="1.4"/><path d="M1.5 3.5 L7 8 L12.5 3.5" fill="none" stroke="#f37122" stroke-width="1.4"/></svg>
        <span>Dana@larkwellnow.com</span>
      </li>
      <li class="contact-item">
        <svg viewBox="0 0 14 14" aria-hidden="true"><circle cx="7" cy="7" r="5.8" fill="none" stroke="#f37122" stroke-width="1.4"/><ellipse cx="7" cy="7" rx="2.5" ry="5.8" fill="none" stroke="#f37122" stroke-width="1.2"/><path d="M1.2 7 H12.8" stroke="#f37122" stroke-width="1.2"/></svg>
        <span>www.<span class="web-name">larkwellnow</span>.com</span>
      </li>
    </ul>
  </section>

  <section class="card card-back">
    <div class="map-area" role="img" aria-label="Faint dotted world map background"></div>
    <div class="back-brand">
      <span class="brand-dot"></span>
      <span class="brand-name">Larkwell</span>
    </div>
    <p class="offer">Get your free Larkwell<br>Starter Package and our marketing guide today at</p>
    <div class="back-rule"></div>
    <p class="tagline">REACH MORE PEOPLE. MAKE MORE MONEY. CREATE MORE IMPACT.</p>
  </section>
</body>
</html>
```